Business Card Design Project

I require a business card with the following information on them for various different people;
name
m:
f:
e:
I have a logo already and will attached that. We are in the construction industry. I require something clean and simple but eye catching at the same time. You can use another colour with our logo if you like and you can style the logo as well if you wish. I am open.
Also it needs to be front and back design.
Industry/Entity Type
Construction
Requirements
Must have
- Logo, name, mobile, fax and email address.
Front and back design

```html
<!DOCTYPE html>
<html lang="en">
<head>
<meta charset="utf-8">
<title>Keystone Ridge Developments – Business Card</title>
<link rel="stylesheet" href="https://fonts.googleapis.com/css2?family=Arimo:wght@400&display=swap">
<style>
  :root {
    --stage-top: #ffffff;
    --stage-bottom: #dde2e2;
    --card-white: #ffffff;
    --lime: #9be51c;
    --lime-light: #b9f326;
    --lime-deep: #8fe41a;
    --ink: #5a6163;
    --ink-dark: #3f4647;
  }
  * { margin: 0; padding: 0; box-sizing: border-box; }
  html, body {
    width: 1200px;
    height: 1200px;
    overflow: hidden;
  }
  body {
    position: relative;
    background: linear-gradient(to bottom, var(--stage-top) 12%, var(--stage-bottom) 100%);
    font-family: "Arimo", Arial, sans-serif;
  }
  .card {
    position: absolute;
  }
  .card-front {
    left: 246px;
    top: 184px;
    width: 708px;
    height: 398px;
    background: var(--card-white);
  }
  .brand {
    position: absolute;
    left: 36px;
    top: 36px;
    display: flex;
    align-items: center;
    gap: 22px;
  }
  .brand-square {
    width: 86px;
    height: 86px;
    background: var(--lime);
  }
  .brand-name {
    color: var(--ink-dark);
    font-weight: 400;
    line-height: 1;
  }
  .brand-name .line-main {
    display: block;
    font-size: 58px;
    letter-spacing: -0.5px;
  }
  .brand-name .line-sub {
    display: block;
    font-size: 23px;
    letter-spacing: 7px;
    margin-top: 6px;
  }
  .brand-rule {
    position: absolute;
    left: 36px;
    top: 156px;
    width: 560px;
    height: 3px;
    background: linear-gradient(to right, var(--lime) 0%, var(--lime) 40%, rgba(155, 229, 28, 0) 100%);
  }
  .contact {
    position: absolute;
    right: 58px;
    top: 174px;
    text-align: right;
    color: var(--ink);
  }
  .contact-name {
    font-size: 25px;
    color: var(--lime);
    margin-bottom: 27px;
  }
  .contact-line {
    font-size: 21px;
    margin-bottom: 26px;
  }
  .contact-line .label {
    color: var(--lime);
  }
  .card-back {
    left: 249px;
    top: 669px;
    width: 702px;
    height: 401px;
    background: linear-gradient(to bottom, var(--lime-light) 0%, var(--lime-deep) 100%);
  }
  .back-brand {
    position: absolute;
    left: 52px;
    bottom: 48px;
    display: flex;
    align-items: center;
    gap: 20px;
  }
  .back-square {
    width: 120px;
    height: 120px;
    background: var(--card-white);
  }
  .back-name {
    color: var(--card-white);
    font-size: 30px;
    line-height: 1.15;
  }
</style>
</head>
<body>
  <section class="card card-front" aria-label="Business card front">
    <div class="brand">
      <div class="brand-square"></div>
      <div class="brand-name">
        <span class="line-main">Keystone Ridge</span>
        <span class="line-sub">DEVELOPMENTS</span>
      </div>
    </div>
    <div class="brand-rule"></div>
    <div class="contact">
      <p class="contact-name">Alex Carter</p>
      <p class="contact-line"><span class="label">M:</span> 555.555.0142</p>
      <p class="contact-line"><span class="label">F:</span> 555.555.0143</p>
      <p class="contact-line">AlexCarter@KeystoneRidge.com</p>
    </div>
  </section>

  <section class="card card-back" aria-label="Business card back">
    <div class="back-brand">
      <div class="back-square"></div>
      <p class="back-name">Keystone Ridge<br>Developments</p>
    </div>
  </section>
</body>
</html>
```